Redesign Craft Brewing Recipe Website

Originally built with Bootstrap just to get the site going, I am seeking a complete redesign of the sites home page and recipe page. I am an experienced web developer with no graphic background, initially just looking for psd mocks.

I prefer styles that are clean and modern, and would prefer anything that is fun, engaging, and has an organic feel to it. I currently have a cartoon rabbit as a logo, but it needs some modification/tweaking, so any help in that area would be great as well.

Current site:
http://velvetfinch.cloudpagehost.net/

Current launch page/logo:
http://www.velvetfinch.com/

I like the overall layout of the elements currently, but the design sucks.

The launch page is at the following URL

Reason: Still looking for a more modern design. Designs received so far are too similar to the original.

My site is content based and does not contain images or products. Your design should not consist of large images.

Reason: The website has very little images, so the designs need to be more text and content based. The header needs to be very small and should not contain an ad rotater.

Target Market(s)

Home brewers, Craft brewers, Microbreweries, Brewpubs

Requirements
Must have
• Web 2.0 Look and Feel, Fun, Hip, Focus on content
Should not have
• A large photo as a header

```html
<!DOCTYPE html>
<html lang="en">
<head>
<meta charset="utf-8">
<title>Velvetfinch – Recent Recipes</title>
<link rel="stylesheet" href="https://fonts.googleapis.com/css2?family=Titillium+Web:wght@400;600;700&family=PT+Sans:wght@400;700&display=swap">
<style>
  :root {
    --header-bg: #3d3d3d;
    --footer-bg: #222222;
    --page-bg: #ffffff;
    --accent-red: #ff0a0a;
    --accent-orange: #ff8419;
    --tag-grey: #808080;
    --swatch-dark: #4a4a4a;
    --text-dark: #111111;
    --text-body: #555555;
    --text-soft: #666666;
    --rule: #c8c8c8;
    --box-border: #d6d6d6;
    --panel-border: #d0d0d0;
  }
  * { box-sizing: border-box; margin: 0; padding: 0; }
  html, body { width: 1200px; height: 931px; overflow: hidden; }
  body {
    position: relative;
    background: var(--page-bg);
    font-family: "PT Sans", Arial, sans-serif;
    color: var(--text-body);
  }

  /* Header */
  .site-header { position: absolute; left: 0; top: 0; width: 1200px; height: 110px; background: var(--header-bg); }
  .brand { position: absolute; left: 132px; top: 36px; display: flex; align-items: center; gap: 12px; }
  .brand-mark { width: 44px; height: 44px; border-radius: 50%; background: #ffffff; }
  .brand-name { font-family: "Titillium Web", sans-serif; font-weight: 700; font-size: 25px; color: #ffffff; letter-spacing: 0.3px; }
  .main-nav a {
    position: absolute; top: 46px; height: 30px; line-height: 30px;
    font-family: "Titillium Web", sans-serif; font-weight: 600; font-size: 14px;
    color: #ffffff; text-decoration: none; text-align: center;
  }
  .main-nav a.is-active { background: var(--accent-red); border-radius: 3px; }

  /* Sidebar */
  .filter-panel {
    position: absolute; left: 131px; top: 151px; width: 210px; height: 690px;
    border: 1px solid var(--panel-border); border-radius: 8px;
    background: linear-gradient(90deg, #fafafa 0%, #f1f1f1 75%, #e4e4e4 100%);
  }
  .search-box {
    position: absolute; left: 11px; top: 26px; width: 183px; height: 26px;
    border: 1px solid #cfcfcf; background: #fff; border-radius: 2px;
    font-size: 13px; color: #aaa; padding: 5px 0 0 16px;
  }
  .search-box svg { position: absolute; right: 9px; top: 6px; }
  .scroll-track { position: absolute; left: 197px; top: 103px; width: 10px; height: 168px; border: 1px solid #b5b5b5; border-radius: 5px; background: #f4f4f4; }
  .filter-group { position: absolute; left: 17px; }
  .filter-group h3 { font-family: "Titillium Web", sans-serif; font-weight: 400; font-size: 17px; color: #333; letter-spacing: 0.4px; margin-bottom: 6px; }
  .filter-group ul { list-style: none; }
  .filter-group li { display: flex; align-items: center; height: 22px; font-size: 13px; color: var(--text-soft); }
  .radio { width: 11px; height: 11px; border-radius: 50%; border: 1px solid #9a9a9a; background: linear-gradient(#fff, #ddd); margin-right: 9px; position: relative; }
  .radio.is-checked::after { content: ""; position: absolute; left: 2px; top: 2px; width: 5px; height: 5px; border-radius: 50%; background: #111; }
  .panel-divider { position: absolute; left: 35px; width: 140px; height: 1px; background: linear-gradient(90deg, transparent, #e2d6c0, transparent); }

  /* Tabs */
  .recipe-tabs { position: absolute; left: 370px; top: 152px; width: 690px; height: 30px; }
  .tab-active { position: absolute; left: 0; top: 0; width: 134px; height: 29px; line-height: 28px; background: var(--accent-red); color: #fff; border-radius: 4px; text-align: center; font-family: "Titillium Web", sans-serif; font-size: 17px; }
  .tab { position: absolute; left: 148px; top: 0; line-height: 28px; color: #777; font-family: "Titillium Web", sans-serif; font-size: 17px; }
  .tab-rule { position: absolute; left: 280px; top: 18px; width: 409px; height: 1px; background: var(--rule); }

  /* Recipe cards */
  .recipe { position: absolute; left: 370px; width: 690px; height: 134px; }
  .recipe-photo { position: absolute; left: 0; top: 0; width: 72px; height: 70px; border-radius: 6px; }
  .recipe-title { position: absolute; left: 84px; top: -1px; font-size: 15px; font-weight: 400; color: var(--text-dark); letter-spacing: 0.2px; }
  .recipe-desc { position: absolute; left: 85px; top: 22px; width: 605px; font-size: 11.5px; line-height: 14px; color: var(--text-body); }
  .recipe-author { position: absolute; left: 85px; top: 55px; font-size: 11.5px; color: var(--text-body); }
  .recipe-author a { color: var(--accent-red); text-decoration: none; }
  .tag { position: absolute; top: 90px; height: 24px; line-height: 24px; color: #fff; font-size: 12px; font-weight: 700; text-align: center; border-radius: 2px; }
  .tag-method { left: 2px; width: 84px; }
  .tag-style { left: 98px; width: 138px; background: var(--tag-grey); }
  .stats { position: absolute; left: 433px; top: 75px; display: flex; gap: 1px; }
  .stat { width: 50px; height: 38px; border: 1px solid var(--box-border); text-align: center; font-size: 11px; line-height: 13px; color: var(--text-body); padding-top: 5px; }
  .swatch { width: 50px; height: 38px; border: 1px solid var(--box-border); }
  .recipe-rule { position: absolute; left: 1px; width: 689px; height: 1px; background: var(--rule); }
  .is-orange { background: var(--accent-orange); }
  .is-red { background: var(--accent-red); }
  .is-dark { background: var(--swatch-dark); }

  /* Footer */
  .site-footer { position: absolute; left: 0; top: 875px; width: 1200px; height: 56px; background: var(--footer-bg); color: #fff; font-size: 12px; }
  .site-footer span { position: absolute; top: 20px; }
</style>
</head>
<body>
  <header class="site-header">
    <div class="brand">
      <span class="brand-mark"></span>
      <span class="brand-name">VELVETFINCH</span>
    </div>
    <nav class="main-nav">
      <a href="#" class="is-active" style="left:520px;width:74px;">HOME</a>
      <a href="#" style="left:625px;width:80px;">ABOUT US</a>
      <a href="#" style="left:746px;width:70px;">RECIPIES</a>
      <a href="#" style="left:857px;width:80px;">COMPANY</a>
      <a href="#" style="left:978px;width:98px;">CONTACT US</a>
    </nav>
  </header>

  <aside class="filter-panel">
    <div class="search-box">Search
      <svg width="12" height="12" viewBox="0 0 12 12"><circle cx="4.5" cy="4.5" r="3.3" fill="none" stroke="#111" stroke-width="1.6"/><line x1="7" y1="7" x2="11" y2="11" stroke="#111" stroke-width="2"/></svg>
    </div>
    <div class="scroll-track"></div>
    <div class="filter-group" style="top:70px;">
      <h3>BREWING</h3>
      <ul>
        <li><span class="radio"></span>Extract</li>
        <li><span class="radio"></span>Partial Mash</li>
        <li><span class="radio is-checked"></span>All Grain</li>
      </ul>
    </div>
    <div class="panel-divider" style="top:189px;"></div>
    <div class="filter-group" style="top:208px;">
      <h3>STYLES</h3>
      <ul>
        <li><span class="radio"></span>American Amber Ale</li>
        <li><span class="radio"></span>American Barleywine</li>
        <li><span class="radio"></span>American Brown Ale</li>
        <li><span class="radio"></span>American IPA</li>
        <li><span class="radio"></span>American Pale Ale</li>
        <li><span class="radio"></span>American Stout</li>
        <li><span class="radio"></span>American Wheat or Beer</li>
        <li><span class="radio"></span>Applewine</li>
      </ul>
    </div>
    <div class="panel-divider" style="top:440px;"></div>
    <div class="filter-group" style="top:459px;">
      <h3>MATCH MAKER</h3>
      <ul>
        <li><span class="radio"></span>Boil Size</li>
      </ul>
    </div>
  </aside>

  <div class="recipe-tabs">
    <span class="tab-active">Recent Recipies</span>
    <span class="tab">Popular Recipies</span>
    <span class="tab-rule"></span>
  </div>

  <article class="recipe" style="top:210px;">
    <div class="recipe-photo" role="img" aria-label="Photo of a glass of amber ale beside a bottle" style="background:linear-gradient(135deg,#e8e4dc,#a86a28 55%,#3a4a2a);"></div>
    <h2 class="recipe-title">Venom Belgian Specality Ale</h2>
    <p class="recipe-desc">Lorem Ipsum is simply dummy text of the printing and types typesetting industry Ipsum is simply dummy text of the printing.</p>
    <p class="recipe-author">created by <a href="#">Marcus Hale</a></p>
    <span class="tag tag-method is-orange">Partial Mash</span>
    <span class="tag tag-style">Belgian Speciality Ale</span>
    <div class="stats">
      <div class="stat">13.93%<br>abv</div><div class="stat">126<br>ibu</div><div class="stat">1.036<br>fg</div><div class="stat">1.139<br>og</div><div class="swatch is-dark"></div>
    </div>
    <div class="recipe-rule" style="top:133px;"></div>
  </article>

  <article class="recipe" style="top:366px;">
    <div class="recipe-photo" role="img" aria-label="Photo of a glass of dark ale" style="background:linear-gradient(135deg,#c8b8a0,#3a2418 55%,#8a6a48);"></div>
    <h2 class="recipe-title">Venom Belgian Specality Ale</h2>
    <p class="recipe-desc">Lorem Ipsum is simply dummy text of the printing and types typesetting industry Ipsum is simply dummy text of the printing.</p>
    <p class="recipe-author">created by <a href="#">Marcus Hale</a></p>
    <span class="tag tag-method is-red">Partial Mash</span>
    <span class="tag tag-style">Belgian Speciality Ale</span>
    <div class="stats">
      <div class="stat">13.93%<br>abv</div><div class="stat">126<br>ibu</div><div class="stat">1.036<br>fg</div><div class="stat">1.139<br>og</div><div class="swatch is-orange"></div>
    </div>
    <div class="recipe-rule" style="top:140px;"></div>
  </article>

  <article class="recipe" style="top:531px;">
    <div class="recipe-photo" role="img" aria-label="Photo of beer bottles and a glass on a table" style="background:linear-gradient(135deg,#6a6a6a,#2a2a2a 50%,#b8b0a0);"></div>
    <h2 class="recipe-title">Venom Belgian Specality Ale</h2>
    <p class="recipe-desc">Lorem Ipsum is simply dummy text of the printing and types typesetting industry Ipsum is simply dummy text of the printing.</p>
    <p class="recipe-author">created by <a href="#">Marcus Hale</a></p>
    <span class="tag tag-method is-orange">Partial Mash</span>
    <span class="tag tag-style">Belgian Speciality Ale</span>
    <div class="stats">
      <div class="stat">13.93%<br>abv</div><div class="stat">126<br>ibu</div><div class="stat">1.036<br>fg</div><div class="stat">1.139<br>og</div><div class="swatch is-dark"></div>
    </div>
    <div class="recipe-rule" style="top:140px;"></div>
  </article>

  <article class="recipe" style="top:699px;">
    <div class="recipe-photo" role="img" aria-label="Photo of a golden pilsner beside its bottle" style="background:linear-gradient(135deg,#e0a050,#c06a18 50%,#3a3024);"></div>
    <h2 class="recipe-title">Venom Belgian Specality Ale</h2>
    <p class="recipe-desc">Lorem Ipsum is simply dummy text of the printing and types typesetting industry Ipsum is simply dummy text of the printing.</p>
    <p class="recipe-author">created by <a href="#">Marcus Hale</a></p>
    <span class="tag tag-method is-red">Partial Mash</span>
    <span class="tag tag-style">Belgian Speciality Ale</span>
    <div class="stats">
      <div class="stat">13.93%<br>abv</div><div class="stat">126<br>ibu</div><div class="stat">1.036<br>fg</div><div class="stat">1.139<br>og</div><div class="swatch is-orange"></div>
    </div>
    <div class="recipe-rule" style="top:140px;"></div>
  </article>

  <footer class="site-footer">
    <span style="left:138px;">Terms of Service</span>
    <span style="left:260px;">|</span>
    <span style="left:299px;">Contact</span>
    <span style="right:141px;">Copyright © 2013 Velvetfinch. All rights reserved.</span>
  </footer>
</body>
</html>
```